Very new and innovative Web design for Property managers of Vacation rentals

We are looking for a new website design for travel agencies and property managers specialised on vacation rentals business, holiday villas and apartments.

The end users of this website are travellers who are looking for a vacation home for their next holiday: this is the reason why the website must be easy to use, attractive, professional, possibly elegant and focused on get new reservations.

This is a draft of our current website: https://intro3.kelumsito.com/
Please consider that we would like to have proposals with a totally different and innovative layout, surprise us!

These are the pages of the website:
• Homepage: feel free to redesign all the homepage as you wish, surprise us with something very new! Please consider that Property manager/Travel agencies usually want to have the opportunity to put in evidence groups of houses with specific characteristics (eg. villas with private swimming pool, apartment in big/small towns, villas with air co, etc…), destinations and tourist areas, and sometimes experiences or activities (please consider that the website layout must be suitable even if some of the previous sections are not used).
• Search page: we’d like to organise the results of the search page in three different ways:
o Grid
o Map
o List
• Property page: to illustrate the characteristics, descriptions, images, …. of the property. It is very important to put in evidence images of the property and to maintain the booking form (and the other call to action bottom – eg. whatsapp) always visible
• Custom pages: static pages composed usually by text, images and call to actions
• Contact us (general form)
• Info request (specific of a property form)
• Booking process
• Blog, organised in four pages:
o Home Page – introduction to the blog
o List of articles
o Single article
o Site Map (presentation of categories and sub-categories)

If possible, we’d prefer to receive the material in Adobe XD or similar so that we can obtain the three versions:
- smartphone
- tablet
- desktop

The website will be then developed in Bootstrap: as a result we’ll need the icons in SVG format (or the library used)

In attachment you can find the map of the website pages

```html
<!DOCTYPE html>
<html lang="en">
<head>
<meta charset="utf-8">
<title>Blog Details – StayNest</title>
<link href="https://fonts.googleapis.com/css2?family=Mulish:wght@400;600;700&family=Playfair+Display:wght@400;700&display=swap" rel="stylesheet">
<style>
:root{
  --green:#0db585;
  --ink:#1c1c1c;
  --text:#555;
  --muted:#777;
  --line:#dcdcdc;
  --footer:#1b1b1b;
  --footer-text:#bbb;
  --white:#fff;
}
*{box-sizing:border-box;margin:0;padding:0}
html,body{width:687px;height:1200px;overflow:hidden;background:var(--white)}
body{position:relative;font-family:"Mulish",sans-serif;color:var(--ink)}
.abs{position:absolute}
.serif{font-family:"Playfair Display",serif}

/* header */
.topbar{left:463px;top:0;width:224px;height:24px;background:var(--green);clip-path:polygon(0 0,100% 0,100% 100%,24px 100%)}
.topbar-links{right:34px;top:0;height:24px;display:flex;align-items:center;gap:14px;font-size:6.5px;font-weight:700;color:var(--white)}
.topbar-links span{display:flex;align-items:center;gap:3px}
.brand{left:64px;top:15px;display:flex;align-items:center;gap:5px;font-size:16px;color:var(--green);font-weight:600}
.brand-mark{width:22px;height:22px;border-radius:50%;background:var(--green)}
.main-nav{right:64px;top:34px;display:flex;gap:31px;font-size:7.5px;color:#333;letter-spacing:.2px}

/* hero */
.hero{left:0;top:53px;width:687px;height:163px;background:linear-gradient(90deg,#8e8a7c 0%,#6f6d62 30%,#3f4f3d 55%,#2f4a63 75%,#365f85 100%)}
.hero-title{left:0;top:118px;width:687px;text-align:center;font-size:26px;font-weight:700;color:var(--white);letter-spacing:.3px}

.crumbs{left:64px;top:234px;font-size:7px;color:var(--muted)}
.crumbs b{font-weight:400;color:var(--ink)}

/* article */
.post-photo{left:65px;top:271px;width:319px;height:224px;border-radius:4px;background:linear-gradient(135deg,#8a2a2a 0%,#c99a62 40%,#e3c89a 60%,#6e4a33 100%)}
.post-meta{left:64px;top:502px;font-size:7px;display:flex;gap:8px}
.post-title{left:64px;top:522px;width:300px;font-size:16px;line-height:18.5px;color:var(--ink);font-weight:400}
.post-body{left:64px;top:572px;width:366px;font-size:7.6px;line-height:13.6px;color:var(--text)}
.share{left:64px;top:672px;display:flex;gap:2.6px}
.share span{width:18px;height:18px;border:1px solid var(--line);display:flex;align-items:center;justify-content:center}
.share i{width:6px;height:6px;border-radius:50%;background:#333;display:block}

/* comment form */
.section-title{font-size:12px;color:var(--ink);letter-spacing:.2px;font-weight:400}
.field{border:1px solid var(--line);font-size:6px;color:#555;padding:7px 5px 0}
.check{left:64px;top:818px;display:flex;align-items:center;gap:4px;font-size:6px;color:var(--muted)}
.check i{width:7px;height:7px;border:1px solid var(--line);display:block}
.btn{left:64px;top:946px;width:75px;height:26px;background:var(--green);color:var(--white);font-size:7px;font-weight:700;display:flex;align-items:center;justify-content:center}

/* sidebar */
.widget{left:482px;width:138px;border:1px solid var(--line)}
.widget h3{position:absolute;left:9px;font-family:"Playfair Display",serif;font-weight:400;font-size:12px;color:var(--ink)}
.cat-list{position:absolute;left:10px;top:38px;width:113px;list-style:none;font-size:7.3px;color:var(--ink)}
.cat-list li{height:23.5px;display:flex;justify-content:space-between}
.search{position:absolute;left:7px;top:35px;width:122px;height:21px;border:1px solid #999;border-radius:4px;font-size:6.5px;color:var(--muted);display:flex;align-items:center;justify-content:space-between;padding:0 7px}
.tags{position:absolute;left:7px;top:33px;width:122px;display:flex;flex-wrap:wrap;gap:3px 2px}
.tags span{width:39px;height:19px;border:1px solid var(--line);font-size:5.8px;color:#555;display:flex;align-items:center;justify-content:center}

/* footer */
.footer{left:0;top:1007px;width:687px;height:193px;background:var(--footer)}
.foot-brand{left:64px;top:1078px;display:flex;align-items:center;gap:5px;font-size:13px;color:var(--green);font-weight:600}
.foot-brand i{width:18px;height:18px;border-radius:50%;background:var(--green);display:block}
.foot-col{top:1034px;font-size:7.3px;color:var(--footer-text)}
.foot-col h4{font-family:"Playfair Display",serif;font-weight:400;font-size:10.5px;color:var(--white);margin-bottom:10px}
.foot-col ul{list-style:none}
.foot-col li{height:16px}
.contact li{display:flex;gap:4px;height:auto;margin-bottom:13px;line-height:9.5px}
.follow li{display:flex;align-items:center;gap:5px;height:19.5px}
.follow i{width:16px;height:16px;border-radius:50%;background:var(--white);display:block}
.copyright{left:0;top:1152px;width:687px;text-align:center;font-size:6.5px;color:var(--footer-text)}
.copyright b{font-weight:400;color:var(--white)}
</style>
</head>
<body>

<header>
  <div class="abs topbar"></div>
  <div class="abs topbar-links">
    <span><svg width="7" height="7" viewBox="0 0 10 10"><circle cx="5" cy="3" r="2.3" fill="none" stroke="#fff"/><path d="M1 10c0-3 8-3 8 0" fill="none" stroke="#fff"/></svg>LOGIN</span>
    <span><svg width="8" height="7" viewBox="0 0 10 9"><path d="M5 8.5L1 4.5C-.5 2.5 2-1 5 2c3-3 5.5.5 4 2.5z" fill="none" stroke="#fff"/></svg>WHISHLIST</span>
    <span>EN ˅</span>
  </div>
  <div class="abs brand"><span class="brand-mark"></span>StayNest</div>
  <nav class="abs main-nav"><span>HOME</span><span>SEARCH</span><span>PROPERTY</span><span>CUSTOM</span><span>CONTACT US</span></nav>
</header>

<div class="abs hero" role="img" aria-label="Seaside stone castle on a cliff with a yacht on the sea"></div>
<h1 class="abs hero-title serif">BLOG DETAILS</h1>

<div class="abs crumbs">Home &nbsp;/&nbsp; Blog &nbsp;/&nbsp; <b>Blog Details</b></div>

<article>
  <div class="abs post-photo" role="img" aria-label="Hotel receptionist assisting a guest at the front desk"></div>
  <div class="abs post-meta"><span>Marta Rell</span><span>I</span><span>December 4, 2020</span><span>I</span><span>0 Comments</span></div>
  <h2 class="abs post-title serif">One who avoids a pain that produces no resultant pleasure</h2>
  <p class="abs post-body">Sed ut perspiciatis unde omnis iste natus error sit voluptatem accusantium doloremque laudantium, totam rem aperiam, eaque ipsa quae ab illo inventore veritatis et quasi architecto beatae vitae dicta sunt explicabo. Nemo enim ipsam voluptatem quia voluptas sit aspernatur aut odit aut fugit, sed quia consequuntur magni dolores eos qui ratione voluptatem sequi nesciunt. Neque porro quisquam est, qui dolorem ipsum quia dolor sit amet, consectetur, adipisci velit, sed quia non numquam eius modi tempora incidunt ut labore et dolore magnam aliquam quaerat voluptatem.</p>
  <div class="abs share"><span><i></i></span><span><i></i></span><span><i></i></span><span><i></i></span><span><i></i></span><span><i></i></span></div>
</article>

<section class="comment-form">
  <h3 class="abs section-title serif" style="left:64px;top:748px">LEAVE COMMENT</h3>
  <div class="abs field" style="left:64px;top:779px;width:137px;height:23px">Your Name:</div>
  <div class="abs field" style="left:205px;top:779px;width:137px;height:23px">Email:</div>
  <div class="abs check"><i></i>Save my name, email, and website in this browser for the next time I comment.</div>
  <div class="abs field" style="left:64px;top:841px;width:137px;height:23px">Phone:</div>
  <div class="abs field" style="left:205px;top:841px;width:137px;height:23px">Website:</div>
  <div class="abs field" style="left:64px;top:873px;width:278px;height:67px">Comments:</div>
  <div class="abs btn">Post Comments</div>
</section>

<aside>
  <div class="abs widget" style="top:285px;height:276px">
    <h3 style="top:11px">CATEGORIES</h3>
    <ul class="cat-list">
      <li><span>Consectetur Adipiscing</span><span>+</span></li>
      <li><span>Eget Tempor</span><span>+</span></li>
      <li><span>Lobortis Dictum</span><span>+</span></li>
      <li><span>Tempus Fermentum</span><span>+</span></li>
      <li><span>Quisque</span><span>+</span></li>
      <li><span>Consectetur Adipiscing</span><span>+</span></li>
      <li><span>Eget Tempor</span><span>+</span></li>
      <li><span>Lobortis Dictum</span><span>+</span></li>
      <li><span>Tempus Fermentum</span><span>+</span></li>
      <li><span>Quisque</span><span>+</span></li>
    </ul>
  </div>
  <div class="abs widget" style="top:580px;height:73px">
    <h3 style="top:11px">SEARCH</h3>
    <div class="search">Search here<svg width="9" height="9" viewBox="0 0 10 10"><circle cx="4.3" cy="4.3" r="3.3" fill="none" stroke="#111" stroke-width="1.3"/><path d="M6.8 6.8L9.3 9.3" stroke="#111" stroke-width="1.3"/></svg></div>
  </div>
  <div class="abs widget" style="top:673px;height:110px">
    <h3 style="top:9px">POPULAR TAGS</h3>
    <div class="tags"><span>AGENCY</span><span>BUSINESS</span><span>CLEAN</span><span>CREATIVE</span><span>DESIGN</span><span>MODERN</span><span>POPULAR</span></div>
  </div>
</aside>

<footer>
  <div class="abs footer"></div>
  <div class="abs foot-brand"><i></i>StayNest</div>
  <div class="abs foot-col" style="left:191px"><h4>Quick Links</h4><ul><li>Home</li><li>Search</li><li>Property</li><li>Custom</li><li>Contact Us</li></ul></div>
  <div class="abs foot-col" style="left:300px"><h4>Company</h4><ul><li>Privacy Policies</li><li>Reservation Policies</li><li>Cookie Policy</li></ul></div>
  <div class="abs foot-col contact" style="left:416px"><h4>Contact Us</h4><ul>
    <li><svg width="6" height="8" viewBox="0 0 6 8"><path d="M3 8C1 5 0 4 0 3a3 3 0 016 0c0 1-1 2-3 5z" fill="#fff"/><circle cx="3" cy="3" r="1" fill="#1b1b1b"/></svg><span>Via dei Tigli 42 50120<br>Borgo Sereno, Valdarno (Italy)</span></li>
    <li><svg width="6" height="8" viewBox="0 0 6 8"><path d="M1 0h1.5l.5 2-1 .8c.3 1.2 1 2 1.8 2.4L4.6 4.3 6 5.2V7c-3 .5-6-3-5-7z" fill="#fff"/></svg><span>+39 055 0142 870</span></li>
    <li><svg width="8" height="6" viewBox="0 0 8 6"><rect width="8" height="6" fill="#fff"/><path d="M0 0l4 3.2L8 0" fill="none" stroke="#1b1b1b" stroke-width=".8"/></svg><span>hello@staynest-rentals.com</span></li>
  </ul></div>
  <div class="abs foot-col follow" style="left:565px"><h4>Follow Us</h4><ul><li><i></i>Community</li><li><i></i>Newsroom</li><li><i></i>Gallery</li></ul></div>
  <div class="abs copyright">Copyright © 2021 <b>StayNest</b>. All rights reserved.</div>
</footer>

</body>
</html>
```